QVR business card

Need a business card for a company that provides instructional design and elearning development services. The website is here: http://quorvane.studio/

I'm attaching a current logo, as well as the old business card design. While I like to keep it clean, the old design is too simplistic for my liking. The only idea I want to reuse from the old design is placing industry jargon on the back of the card, just need a better way to present it. But if you have other ideas for the back--feel free to experiment.

Please use the colors complementary to the color we have on the website. Thank you!

```html
<!DOCTYPE html>
<html lang="en">
<head>
<meta charset="utf-8">
<title>QVR business card</title>
<link rel="stylesheet" href="https://fonts.googleapis.com/css2?family=Roboto+Slab:wght@500;600&family=Roboto:wght@400;500&display=swap">
<style>
  :root {
    --backdrop: #a9a7a7;
    --card: #333334;
    --gold: #d8cf80;
    --teal: #1eb5a0;
    --grey-text: #a9a9ab;
    --soft-text: #c2c2c4;
    --divider: #5a5a5c;
    --white: #f2f2f2;
  }
  * { margin: 0; padding: 0; box-sizing: border-box; }
  html, body { width: 1200px; height: 1200px; overflow: hidden; }
  body { background: var(--backdrop); position: relative; font-family: "Roboto", Arial, sans-serif; }

  .card {
    position: absolute;
    width: 714px;
    height: 418px;
    background: var(--card);
    border-radius: 28px;
    overflow: hidden;
  }
  .card--front { left: 238px; top: 118px; }
  .card--back  { left: 231px; top: 645px; }

  /* Front: headline */
  .headline { position: absolute; inset: 0; font-family: "Roboto Slab", Georgia, serif; font-weight: 500; }
  .headline span { position: absolute; line-height: 1; white-space: nowrap; }
  .headline__how  { left: 248px; top: 102px; font-size: 76px; color: var(--gold); }
  .headline__can  { left: 186px; top: 156px; font-size: 76px; color: var(--grey-text); }
  .headline__we   { left: 352px; top: 172px; font-size: 50px; color: var(--teal); }
  .headline__help { left: 258px; top: 232px; font-size: 78px; color: var(--gold); }
  .headline__mark { left: 455px; top: 128px; font-size: 196px; font-weight: 600; color: var(--teal); }

  /* Back: brand */
  .brand {
    position: absolute; left: 60px; top: 160px; width: 255px;
    display: flex; align-items: center; justify-content: center; gap: 14px;
  }
  .brand__dot { width: 26px; height: 26px; border-radius: 50%; background: var(--teal); }
  .brand__name {
    font-family: "Roboto Slab", Georgia, serif; font-weight: 600;
    font-size: 64px; color: var(--gold); line-height: 1;
  }

  .divider { position: absolute; left: 361px; top: 47px; width: 2px; height: 280px; background: var(--divider); }

  .person { position: absolute; left: 397px; top: 113px; }
  .person__name { font-size: 21px; font-weight: 500; color: var(--grey-text); letter-spacing: 0.3px; }
  .person__role { margin-top: 8px; font-size: 16px; color: var(--grey-text); }

  .contacts { position: absolute; left: 397px; top: 205px; list-style: none; }
  .contacts li { display: flex; align-items: center; height: 28px; font-size: 17.5px; color: var(--soft-text); }
  .contacts svg { width: 17px; height: 17px; margin-right: 18px; flex: none; }

  .bands { position: absolute; left: 0; bottom: 0; width: 714px; height: 44px; }
  .email {
    position: absolute; left: 330px; right: 0; bottom: 10px;
    text-align: center; font-size: 18px; color: var(--white); letter-spacing: 0.2px;
  }
</style>
</head>
<body>

  <section class="card card--front" aria-label="Card front">
    <h1 class="headline">
      <span class="headline__how">How</span>
      <span class="headline__can">can</span>
      <span class="headline__we">we</span>
      <span class="headline__help">Help</span>
      <span class="headline__mark">?</span>
    </h1>
  </section>

  <section class="card card--back" aria-label="Card back">
    <div class="brand">
      <span class="brand__dot"></span>
      <span class="brand__name">QVR</span>
    </div>

    <div class="divider"></div>

    <div class="person">
      <p class="person__name">Dana Whitcombe</p>
      <p class="person__role">Managing Director</p>
    </div>

    <ul class="contacts">
      <li>
        <svg viewBox="0 0 20 20" aria-hidden="true"><path fill="#1eb5a0" d="M2 7c0-3 3-4 8-4s8 1 8 4v1h-4V6.5H6V8H2zM5 9h10l2 7H3zm5 2a2 2 0 100 4 2 2 0 000-4z"/></svg>
        555-014-2837
      </li>
      <li>
        <svg viewBox="0 0 20 20" aria-hidden="true"><g fill="none" stroke="#1eb5a0" stroke-width="1.8"><circle cx="10" cy="10" r="8"/><ellipse cx="10" cy="10" rx="3.5" ry="8"/><path d="M2 10h16"/></g></svg>
        www.quorvane.studio
      </li>
    </ul>

    <svg class="bands" viewBox="0 0 714 44" aria-hidden="true">
      <rect x="0" y="15" width="340" height="29" fill="#d8cf80"/>
      <polygon points="342,0 714,0 714,44 312,44" fill="#1eb5a0"/>
    </svg>
    <p class="email">dwhitcombe@quorvane.studio</p>
  </section>

</body>
</html>
```